Help our Sugar Loom find our winning design! We're looking for a business card....

We’re a Sugar Loom in NY specializing in custom-made cakes and unique desserts.
Our cakes combine flavor and art, each designed to match customer’s special event and theme.
We’d like a unique business card with a clean design that will combine French chic and artistic look & feel.
We’d like to differentiate ourselves from standard bakeries, please don’t offer cupcake images :-)
Our logo is peach-pink and brown and we’d love to use these colors ( . Another color that can be added is gold - or feel free to suggest!

Target Market(s)

Women, ages 25-55

Industry/Entity Type

Boutique

Contact Information for Business Card

Text on card:
Logo
Sugar Loom by Dana Welch

www.sugarloomsweets.com
hello@sugarloom.com
(516) 555-0147
F – sugarloomnyc
IG - sugarloom_ny

Font styles to use
Sans Serif
Script

Requirements
Must have
• Logo
• Clean look
• French chic and artistic look & feel.
Nice to have
• Damask pattern
Should not have
• Cupcake images

```html
<!DOCTYPE html>
<html lang="en">
<head>
<meta charset="utf-8">
<title>Sugar Loom – Business Card</title>
<link rel="stylesheet" href="https://fonts.googleapis.com/css2?family=Open+Sans:wght@400;600&family=Pinyon+Script&display=swap">
<style>
  :root {
    --backdrop: #e4e4e4;
    --card: #ffffff;
    --pattern: #f1efef;
    --peach: #e3978a;
    --peach-soft: #f6e3e0;
    --brown: #3a2a26;
    --ink: #2f2f2f;
    --gold-dark: #8a6a1c;
    --gold-light: #e0bd52;
  }
  * { box-sizing: border-box; margin: 0; padding: 0; }
  html, body { width: 1200px; height: 852px; overflow: hidden; }
  body {
    background: var(--backdrop);
    font-family: "Open Sans", Arial, sans-serif;
    color: var(--ink);
    position: relative;
  }
  .card {
    position: absolute;
    top: 277px;
    width: 530px;
    height: 298px;
    background: var(--card);
    border-radius: 22px;
    overflow: hidden;
    box-shadow: 0 6px 18px rgba(0,0,0,0.18);
  }
  .card--front { left: 45px; }
  .card--back { left: 625px; }

  /* front */
  .damask-field {
    position: absolute; inset: 0;
    background: radial-gradient(circle at 50% 50%, var(--card) 0%, var(--pattern) 100%);
  }
  .ribbon {
    position: absolute; left: 0; right: 0; top: 132px; height: 36px;
    background: var(--peach);
  }
  .logo-plate {
    position: absolute; left: 130px; top: 78px; width: 270px; height: 144px;
    background: var(--card);
    border: 2px solid var(--peach);
    border-radius: 60px;
    display: flex; align-items: center; justify-content: center; gap: 10px;
  }
  .brand-name {
    font-family: "Pinyon Script", cursive;
    font-size: 46px;
    color: var(--brown);
    line-height: 1;
  }
  .brand-dot {
    width: 10px; height: 10px; border-radius: 50%;
    background: var(--peach);
  }

  /* back */
  .flourish-area {
    position: absolute; left: 20px; top: 40px; width: 180px; height: 170px;
    border-radius: 50%;
    background: radial-gradient(circle, var(--peach-soft) 0%, rgba(246,227,224,0) 70%);
  }
  .back-logo {
    position: absolute; right: 40px; top: 30px; width: 220px; height: 100px;
    border: 1.5px solid var(--peach);
    border-radius: 48px;
    display: flex; align-items: center; justify-content: center; gap: 8px;
  }
  .back-logo .brand-name { font-size: 36px; }
  .gold-rule {
    position: absolute; left: 200px; right: 24px; top: 160px; height: 3px;
    background: linear-gradient(90deg, var(--gold-dark), var(--gold-light), var(--gold-dark));
  }
  .owner {
    position: absolute; left: 34px; top: 175px;
  }
  .owner__line { font-size: 15px; color: var(--ink); }
  .owner__name {
    font-family: "Pinyon Script", cursive;
    font-size: 30px; color: var(--brown); line-height: 1.1;
  }
  .contact {
    position: absolute; left: 34px; top: 236px;
    list-style: none; font-size: 13px; line-height: 19px;
  }
  .contact li, .social li { display: flex; align-items: center; gap: 8px; }
  .contact svg { width: 11px; height: 11px; fill: var(--ink); }
  .social {
    position: absolute; right: 32px; top: 176px;
    list-style: none; font-size: 13px; line-height: 20px;
  }
  .social__mark {
    width: 10px; height: 10px; background: var(--ink); border-radius: 2px;
  }
</style>
</head>
<body>
  <section class="card card--front" aria-label="Card front">
    <div class="damask-field" role="img" aria-label="Soft damask pattern background"></div>
    <div class="ribbon"></div>
    <div class="logo-plate">
      <span class="brand-name">Sugar Loom</span>
      <span class="brand-dot"></span>
    </div>
  </section>

  <section class="card card--back" aria-label="Card back">
    <div class="flourish-area" role="img" aria-label="Faint floral flourish ornament"></div>
    <div class="back-logo">
      <span class="brand-name">Sugar Loom</span>
      <span class="brand-dot"></span>
    </div>
    <div class="gold-rule"></div>

    <div class="owner">
      <p class="owner__line">Sugar Loom by</p>
      <p class="owner__name">Dana Welch</p>
    </div>

    <ul class="contact">
      <li>
        <svg viewBox="0 0 12 12" aria-hidden="true"><path d="M2 1h2.5l1 3-1.5 1a7 7 0 0 0 3 3l1-1.5 3 1V10a1 1 0 0 1-1 1A9 9 0 0 1 1 2a1 1 0 0 1 1-1z"/></svg>
        (516) 555-0147
      </li>
      <li>
        <svg viewBox="0 0 12 12" aria-hidden="true"><path d="M1 2.5h10v7H1z M1 2.5l5 4 5-4" fill="none" stroke="currentColor" stroke-width="1.2"/></svg>
        hello@sugarloom.com
      </li>
      <li>
        <svg viewBox="0 0 12 12" aria-hidden="true"><circle cx="6" cy="6" r="5" fill="none" stroke="currentColor" stroke-width="1.2"/><path d="M1 6h10M6 1c-3 3-3 7 0 10M6 1c3 3 3 7 0 10" fill="none" stroke="currentColor" stroke-width="1"/></svg>
        www.sugarloomsweets.com
      </li>
    </ul>

    <ul class="social">
      <li><span class="social__mark"></span>sugarloomnyc</li>
      <li><span class="social__mark"></span>sugarloom_ny</li>
    </ul>
  </section>
</body>
</html>
```